Home Security Company Business Card

Looking for a eye catching business card that is non traditional and stands out but yet still looks professional. It should include all the pertinent information such as name, title, address, telephone, e-mail, website address should definitely stand out and then finally the logo.

Target Market(s)

Residential and Commercial accounts mostly upscale accounts

Industry/Entity Type

Security

Contact Information for Business Card

Name
Title
Address
Office #
Cell #
E-mail
Website

Font styles to use
Serif
Sans Serif

Requirements
Must have
• Logo, two sided color configuration
Nice to have
• You decide
Should not have
• There really aren't any.

```html
<!DOCTYPE html>
<html lang="en">
<head>
<meta charset="utf-8">
<title>Ironhold Security Group – Business Card</title>
<link rel="stylesheet" href="https://fonts.googleapis.com/css2?family=PT+Sans:ital,wght@0,400;0,700;1,400&display=swap">
<style>
  :root {
    --backdrop: #3b3b3b;
    --card-red: #700d00;
    --card-white: #fbfbfb;
    --gold: #e2a93b;
    --gold-deep: #c98a2c;
    --gold-light: #f0c061;
    --text-light: #ffffff;
  }
  * { margin: 0; padding: 0; box-sizing: border-box; }
  html, body {
    width: 1200px; height: 750px; overflow: hidden;
    background: var(--backdrop);
    font-family: "PT Sans", Arial, sans-serif;
  }
  .canvas { position: relative; width: 1200px; height: 750px; }
  .card {
    position: absolute; top: 228px;
    width: 461px; height: 262px;
    background: var(--card-red);
    overflow: hidden;
  }
  .card--front { left: 144px; }
  .card--back { left: 612px; }
  .card__art { position: absolute; inset: 0; }

  .contact { position: absolute; left: 36px; top: 49px; color: var(--text-light); }
  .contact__name { color: var(--gold); font-size: 17px; font-weight: 700; line-height: 1.1; }
  .contact__title { font-size: 13px; margin-top: 2px; }
  .contact__address { font-size: 11.5px; line-height: 14px; margin-top: 27px; }
  .contact__list { list-style: none; margin-top: 8px; font-size: 11.5px; }
  .contact__item { display: flex; align-items: center; height: 17.5px; }
  .contact__icon { width: 11px; height: 11px; margin-right: 6px; flex: none; }

  .brand {
    position: absolute; left: 268px; top: 110px;
    display: flex; align-items: center; gap: 8px;
    color: var(--card-red); font-weight: 700;
  }
  .brand__dot { width: 14px; height: 14px; border-radius: 50%; background: var(--gold); flex: none; }
  .brand__name { font-size: 15px; line-height: 16px; letter-spacing: 0.5px; }

  .back-brand {
    position: absolute; left: 0; right: 0; top: 100px;
    display: flex; justify-content: center; align-items: center; gap: 10px;
    color: var(--gold); font-weight: 700; font-size: 20px; letter-spacing: 1px;
  }
  .back-brand__dot { width: 18px; height: 18px; border-radius: 50%; background: var(--gold); }
  .back-web {
    position: absolute; left: 0; right: 0; top: 216px;
    text-align: center; color: var(--text-light);
    font-style: italic; font-size: 12px; letter-spacing: 3px;
  }
</style>
</head>
<body>
<main class="canvas">
  <section class="card card--front" aria-label="Card front">
    <svg class="card__art" viewBox="0 0 461 262" aria-hidden="true">
      <defs>
        <linearGradient id="gold-band" x1="0" y1="0" x2="1" y2="1">
          <stop offset="0" stop-color="#e8b04a"/>
          <stop offset="1" stop-color="#c4852b"/>
        </linearGradient>
      </defs>
      <path d="M258,0 C205,40 186,130 208,190 C222,228 244,250 262,262 L461,262 L461,0 Z" fill="var(--card-white)"/>
      <path d="M202,122 C198,190 236,240 268,262 L382,262 C300,240 226,205 202,122 Z" fill="url(#gold-band)"/>
    </svg>

    <div class="contact">
      <p class="contact__name">Daniel Reyes</p>
      <p class="contact__title">CEO/Founder</p>
      <p class="contact__address">4120 Birchwood Court<br>Fairbanks, Alaska 99701</p>
      <ul class="contact__list">
        <li class="contact__item">
          <svg class="contact__icon" viewBox="0 0 12 12"><path d="M2.5 1 L4.5 1 L5.3 3.6 L4 4.6 C4.7 6 6 7.3 7.4 8 L8.4 6.7 L11 7.5 L11 9.5 C11 10.3 10.3 11 9.5 11 C5 11 1 7 1 2.5 C1 1.7 1.7 1 2.5 1 Z" fill="var(--gold)"/></svg>
          907 555 0142
        </li>
        <li class="contact__item">
          <svg class="contact__icon" viewBox="0 0 12 12"><rect x="3" y="0.5" width="6" height="11" rx="1" fill="none" stroke="var(--gold)" stroke-width="1.3"/><rect x="4.3" y="2" width="3.4" height="6.5" fill="var(--gold)"/></svg>
          907 555 0187
        </li>
        <li class="contact__item">
          <svg class="contact__icon" viewBox="0 0 12 12"><rect x="0.5" y="2.5" width="11" height="7" fill="var(--gold)"/><path d="M0.5 2.5 L6 6.5 L11.5 2.5" fill="none" stroke="var(--card-red)" stroke-width="1"/></svg>
          dreyes@ironholdsec.com
        </li>
        <li class="contact__item">
          <svg class="contact__icon" viewBox="0 0 12 12"><circle cx="6" cy="6" r="5.5" fill="var(--gold)"/><path d="M1 6 H11 M6 0.5 C3.5 3 3.5 9 6 11.5 M6 0.5 C8.5 3 8.5 9 6 11.5" fill="none" stroke="var(--card-red)" stroke-width="0.8"/></svg>
          www.ironholdsec.com
        </li>
      </ul>
    </div>

    <div class="brand">
      <span class="brand__dot"></span>
      <span class="brand__name">IRONHOLD<br>SECURITY GROUP</span>
    </div>
  </section>

  <section class="card card--back" aria-label="Card back">
    <div class="back-brand">
      <span class="back-brand__dot"></span>
      <span>IRONHOLD SECURITY GROUP</span>
    </div>
    <p class="back-web">www.ironholdsec.com</p>
  </section>
</main>
</body>
</html>
```